Letter Head for Torin Mase Designer

Wish to have a proper letter head that suits the envelope designs . will prefer the background of the paper got a faded off image and bottom have some designs!

```html
<!DOCTYPE html>
<html lang="en">
<head>
<meta charset="utf-8">
<title>Vega Sole Letterhead</title>
<link href="https://fonts.googleapis.com/css2?family=Open+Sans:wght@400;600&display=swap" rel="stylesheet">
<style>
  :root {
    --paper: #ffffff;
    --ink: #4a4a4a;
    --brand: #1f5f8b;
    --brand-dark: #174a6e;
    --accent: #2a7fc0;
    --swoosh: #e3e5e8;
    --swoosh-line: #c9ccd1;
    --glow: #eef1f5;
  }
  * { margin: 0; padding: 0; box-sizing: border-box; }
  html, body { width: 849px; height: 1200px; overflow: hidden; background: var(--paper); }
  .letterhead {
    position: relative;
    width: 849px; height: 1200px;
    background: var(--paper);
    font-family: "Open Sans", Arial, sans-serif;
    color: var(--ink);
    overflow: hidden;
  }
  .swoosh { position: absolute; left: 0; width: 849px; }
  .swoosh-top { top: 0; height: 220px; }
  .swoosh-bottom { top: 930px; height: 210px; }

  .brand {
    position: absolute; top: 36px; left: 30px;
    display: flex; align-items: center; gap: 14px;
  }
  .brand-dot { width: 64px; height: 64px; border-radius: 50%; background: var(--brand); }
  .brand-name {
    font-weight: 600; font-size: 38px; letter-spacing: 4px;
    text-transform: uppercase; color: var(--brand);
  }

  .sender {
    position: absolute; top: 40px; right: 30px;
    text-align: right; font-size: 15px; line-height: 21px;
  }
  .sender .label { color: var(--accent); font-weight: 600; }

  .watermark-area {
    position: absolute; left: 240px; top: 420px; width: 380px; height: 380px;
    background: radial-gradient(closest-side, var(--glow), rgba(238,241,245,0));
  }

  .footer-band {
    position: absolute; left: 0; bottom: 0; width: 849px; height: 66px;
    background: linear-gradient(var(--brand), var(--brand-dark));
    color: #fff; font-size: 13px;
    display: flex; align-items: center; justify-content: space-between;
    padding: 0 24px;
  }
  .footer-item { display: flex; align-items: center; gap: 7px; line-height: 16px; }
  .footer-item svg { width: 15px; height: 15px; fill: #fff; flex: none; }
</style>
</head>
<body>
<div class="letterhead">
  <svg class="swoosh swoosh-top" viewBox="0 0 849 220" preserveAspectRatio="none">
    <path d="M0 120 C 250 200, 560 210, 849 150 L849 220 L0 220 Z" fill="var(--swoosh)" opacity="0.55"/>
    <path d="M0 110 C 260 180, 560 190, 849 120 L849 150 C 560 210, 250 200, 0 120 Z" fill="var(--swoosh)"/>
    <path d="M0 105 C 270 170, 560 180, 849 110" fill="none" stroke="var(--swoosh-line)" stroke-width="1.5"/>
    <path d="M0 135 C 300 215, 600 210, 849 165" fill="none" stroke="var(--swoosh-line)" stroke-width="1"/>
  </svg>

  <header class="brand">
    <span class="brand-dot"></span>
    <span class="brand-name">Vega Sole</span>
  </header>

  <address class="sender" style="font-style:normal">
    48 Harbour Crest Road<br>
    Northgate 418202<br>
    <span class="label">Ph:</span> 61234570<br>
    <span class="label">Fax:</span> 61234581
  </address>

  <div class="watermark-area" role="img" aria-label="Faded background image area"></div>

  <svg class="swoosh swoosh-bottom" viewBox="0 0 849 210" preserveAspectRatio="none">
    <path d="M0 150 C 260 120, 560 40, 849 20 L849 210 L0 210 Z" fill="var(--swoosh)" opacity="0.5"/>
    <path d="M0 170 C 280 150, 580 80, 849 60 L849 210 L0 210 Z" fill="var(--swoosh)"/>
    <path d="M0 140 C 260 110, 560 30, 849 8" fill="none" stroke="var(--swoosh-line)" stroke-width="1.5"/>
    <path d="M0 185 C 300 165, 600 110, 849 95" fill="none" stroke="var(--swoosh-line)" stroke-width="1"/>
  </svg>

  <footer class="footer-band">
    <div class="footer-item">
      <svg viewBox="0 0 16 16"><path d="M8 0a5.5 5.5 0 0 0-5.5 5.5C2.5 10 8 16 8 16s5.5-6 5.5-10.5A5.5 5.5 0 0 0 8 0zm0 7.8a2.3 2.3 0 1 1 0-4.6 2.3 2.3 0 0 1 0 4.6z"/></svg>
      <span>48 Harbour Crest Road<br>Northgate 418202</span>
    </div>
    <div class="footer-item">
      <svg viewBox="0 0 16 16"><path d="M3.6 1l2.3 3.2-1.4 1.6a9.5 9.5 0 0 0 5.7 5.7l1.6-1.4L15 12.4 13.5 15C7 15 1 9 1 2.5z"/></svg>
      <span>61234570</span>
    </div>
    <div class="footer-item">
      <svg viewBox="0 0 16 16"><path d="M4 1h8v4H4zM1 6h14v6h-3v3H4v-3H1zm4 4v4h6v-4z"/></svg>
      <span>61234581</span>
    </div>
    <div class="footer-item">
      <svg viewBox="0 0 16 16"><path d="M1 3h14v10H1zm1.5 1.2L8 8.5l5.5-4.3z"/></svg>
      <span>hello@vegasole.com</span>
    </div>
    <div class="footer-item">
      <svg viewBox="0 0 16 16"><path d="M8 1a7 7 0 1 0 0 14A7 7 0 0 0 8 1zm0 1.6c.9 1.1 1.5 2.7 1.6 4.6H6.4C6.5 5.3 7.1 3.7 8 2.6zM2.7 8.8h2.3c.1 1.6.5 3 1.1 4.1a5.5 5.5 0 0 1-3.4-4.1zm0-1.6a5.5 5.5 0 0 1 3.4-4.1c-.6 1.1-1 2.5-1.1 4.1zM8 13.4c-.9-1.1-1.5-2.7-1.6-4.6h3.2c-.1 1.9-.7 3.5-1.6 4.6zm1.9-.5c.6-1.1 1-2.5 1.1-4.1h2.3a5.5 5.5 0 0 1-3.4 4.1zM11 7.2c-.1-1.6-.5-3-1.1-4.1a5.5 5.5 0 0 1 3.4 4.1z"/></svg>
      <span>www.vegasole.com</span>
    </div>
  </footer>
</div>
</body>
</html>
```